Business Card Design for Marketing Firm

Looking for business card design for higher end marketing firm. Clean but impressionable/trendy. We are a marketing firm that represents manufacturers in the foodservice equipment and supply industry. Our customers are end users such has hotels, restaurants, country clubs, convention centers and casinos as well as distributors of restaurants supplies and equipment, and manufacturers of foodservice equipment and supplies.
Target Market(s)
Hotels, Restaurants, Supply & Equipment Distributors, Foodservice Manufacturers
Industry/Entity Type
Foodservice/Hospitality
Contact Information for Business Card
Name, Title, Contact Number, Email, Website, Social Media, Address
Requirements
Must have
- Clean & Simple but Serious and Impressionable

```html
<!DOCTYPE html>
<html lang="en">
<head>
<meta charset="utf-8">
<title>Meridian Service Reps – Business Card</title>
<link href="https://fonts.googleapis.com/css2?family=Open+Sans:wght@400;600;700&display=swap" rel="stylesheet">
<style>
  :root {
    --navy: #2a2a78;
    --white: #ffffff;
    --backdrop: #d9d9d6;
    --ink: #1c1c1c;
  }
  * { margin: 0; padding: 0; box-sizing: border-box; }
  html, body { width: 1200px; height: 801px; overflow: hidden; }
  body {
    background: var(--backdrop);
    font-family: "Open Sans", Arial, sans-serif;
    position: relative;
  }
  .card {
    position: absolute;
    top: 257px;
    width: 500px;
    height: 286px;
    border-radius: 16px;
    background: var(--white);
    overflow: hidden;
  }
  .card--front { left: 60px; }
  .card--back { left: 640px; border-bottom: 3px solid var(--navy); border-right: 1px solid var(--navy); }

  .front-arc { position: absolute; inset: 0; width: 500px; height: 286px; }
  .name-tab {
    position: absolute; top: 0; right: 0;
    width: 14px; height: 30px; background: var(--navy);
  }
  .identity { position: absolute; top: 14px; right: 26px; text-align: right; }
  .identity__name { color: var(--navy); font-weight: 700; font-size: 18px; letter-spacing: 0.5px; line-height: 1.15; }
  .identity__title { color: var(--ink); font-size: 11.5px; }

  .contact {
    position: absolute; right: 18px; top: 110px;
    color: var(--white); text-align: right; font-size: 11.5px; line-height: 1.45;
  }
  .contact__address { margin-bottom: 12px; }
  .contact__row { display: flex; justify-content: flex-end; align-items: center; gap: 6px; }
  .contact__row svg { width: 11px; height: 11px; flex: none; }

  .brand { position: absolute; font-weight: 700; color: var(--navy); display: flex; align-items: center; gap: 10px; }
  .brand__dot { width: 14px; height: 14px; border-radius: 50%; background: var(--navy); flex: none; }
  .brand--small { left: 28px; top: 126px; font-size: 20px; letter-spacing: 1px; }
  .brand--large { left: 0; right: 0; top: 100px; justify-content: center; font-size: 30px; letter-spacing: 1.5px; }

  .social { position: absolute; left: 0; right: 0; top: 178px; display: flex; justify-content: center; gap: 5px; }
  .social__item { width: 18px; height: 18px; border-radius: 50%; background: var(--navy); }
</style>
</head>
<body>

<section class="card card--front" aria-label="Card front">
  <svg class="front-arc" viewBox="0 0 500 286" aria-hidden="true">
    <path d="M500 72 C 340 110 225 185 212 286 L500 286 Z" fill="var(--navy)"/>
  </svg>
  <div class="name-tab"></div>
  <div class="identity">
    <p class="identity__name">DANIEL CARTER</p>
    <p class="identity__title">Managing Director</p>
  </div>

  <div class="brand brand--small"><span class="brand__dot"></span>MERIDIAN SERVICE REPS</div>

  <div class="contact">
    <p class="contact__address">Your address, City<br>State, Zip 1234</p>
    <p class="contact__row">123 456 789
      <svg viewBox="0 0 12 12"><path d="M3 1l2 2-1 1.5c.6 1.4 1.6 2.4 3 3L8.5 6.5l2 2L9 10.5C5 10 2 7 1.5 3z" fill="var(--white)"/></svg></p>
    <p class="contact__row">123 456 789
      <svg viewBox="0 0 12 12"><path d="M3 1l2 2-1 1.5c.6 1.4 1.6 2.4 3 3L8.5 6.5l2 2L9 10.5C5 10 2 7 1.5 3z" fill="var(--white)"/></svg></p>
    <p class="contact__row">info@yourmail.com
      <svg viewBox="0 0 12 12"><rect x="1" y="2.5" width="10" height="7" fill="none" stroke="var(--white)" stroke-width="1.2"/><path d="M1 2.5l5 4 5-4" fill="none" stroke="var(--white)" stroke-width="1.2"/></svg></p>
    <p class="contact__row">www.yourwebsite.com
      <svg viewBox="0 0 12 12"><circle cx="6" cy="6" r="5" fill="var(--white)"/></svg></p>
  </div>
</section>

<section class="card card--back" aria-label="Card back">
  <div class="brand brand--large"><span class="brand__dot"></span>MERIDIAN SERVICE REPS</div>
  <div class="social" aria-label="Social media">
    <span class="social__item"></span><span class="social__item"></span><span class="social__item"></span>
    <span class="social__item"></span><span class="social__item"></span><span class="social__item"></span>
  </div>
</section>

</body>
</html>
```